Brightfen Business Card Redesign & Logo Update

We need to update our business cards to something more modern and fresh. Brightfen can provide the current color schemes and old design examples, but welcome creativity in helping us with this redesign. PLEASE NOTE that we no longer utilize the "tree" and/or "leaf" imagery in our branding. If able would apprecaite an update on the quality of our "words only" logo in Ai. / PNG formats too.

Target Market(s)

Investors, landowners, corporate partners, contractors

Industry/Entity Type

Environmental Restoration & Conservation

Contact Information for Business Card

Logo, persons name, title, mailing address, phone and email, website url

Font styles to use
Other font styles liked:
• Merriweather

Requirements
Nice to have
• Logo, persons name, title, mailing address, phone and email, website url, but open to ideams
Should not have
• No all back backgrounds

```html
<!DOCTYPE html>
<html lang="en">
<head>
<meta charset="utf-8">
<title>Brightfen Business Card</title>
<link rel="stylesheet" href="https://fonts.googleapis.com/css2?family=Open+Sans:wght@400;600;700;800&display=swap">
<style>
  :root {
    --orange: #eb7d23;
    --green: #138041;
    --ink: #161616;
    --paper: #ffffff;
    --backdrop: #e9eaec;
    --rule: #222222;
  }
  * { margin: 0; padding: 0; box-sizing: border-box; }
  html, body { width: 1200px; height: 780px; overflow: hidden; }
  body {
    background: var(--backdrop);
    font-family: "Open Sans", Arial, sans-serif;
    color: var(--ink);
    display: flex;
    align-items: center;
    justify-content: center;
    gap: 40px;
  }
  .card {
    position: relative;
    width: 560px;
    height: 320px;
    background: var(--paper);
    border-radius: 22px;
    overflow: hidden;
    box-shadow: 0 6px 18px rgba(0,0,0,0.18);
  }
  .card-swoosh { position: absolute; inset: 0; width: 100%; height: 100%; }
  .swoosh-orange { fill: var(--orange); }
  .swoosh-green { fill: var(--green); }

  .brand {
    position: absolute;
    display: flex;
    flex-direction: column;
    align-items: flex-start;
  }
  .brand-name {
    font-weight: 800;
    color: var(--green);
    letter-spacing: 1px;
    line-height: 1;
    text-transform: uppercase;
  }
  .brand-tagline {
    font-weight: 700;
    color: var(--ink);
    text-transform: uppercase;
    letter-spacing: 0.5px;
    line-height: 1.1;
    margin-top: 6px;
  }
  .card-front .brand { left: 92px; top: 108px; }
  .card-front .brand-name { font-size: 66px; }
  .card-front .brand-tagline { font-size: 17.5px; }

  .card-back .brand { left: 62px; top: 150px; }
  .card-back .brand-name { font-size: 36px; }
  .card-back .brand-tagline { font-size: 9.6px; margin-top: 4px; }

  .divider {
    position: absolute;
    left: 282px;
    top: 60px;
    width: 1px;
    height: 190px;
    background: var(--rule);
  }

  .person { position: absolute; left: 306px; top: 68px; }
  .person-name { font-size: 24px; font-weight: 700; line-height: 1.1; }
  .person-first { color: var(--orange); }
  .person-last { color: var(--green); }
  .person-title { font-size: 13px; font-weight: 400; margin-top: 2px; }

  .contact-list { list-style: none; margin-top: 26px; }
  .contact-item {
    display: flex;
    align-items: center;
    gap: 8px;
    font-size: 12.5px;
    line-height: 1.9;
  }
  .contact-icon { width: 12px; height: 12px; fill: var(--orange); flex: none; }
</style>
</head>
<body>

  <section class="card card-front" aria-label="Business card front">
    <svg class="card-swoosh" viewBox="0 0 560 320" preserveAspectRatio="none" aria-hidden="true">
      <path class="swoosh-orange" d="M0,0 H150 C80,40 45,110 40,205 H0 Z"/>
      <path class="swoosh-green" d="M560,70 C535,200 470,280 400,320 H560 Z"/>
    </svg>
    <div class="brand">
      <span class="brand-name">Brightfen</span>
      <span class="brand-tagline">Environmental Credit Company</span>
    </div>
  </section>

  <section class="card card-back" aria-label="Business card back">
    <svg class="card-swoosh" viewBox="0 0 560 320" preserveAspectRatio="none" aria-hidden="true">
      <path class="swoosh-orange" d="M0,0 H130 C70,40 45,100 40,175 H0 Z"/>
      <path class="swoosh-green" d="M560,85 C540,200 480,275 410,320 H560 Z"/>
    </svg>

    <div class="brand">
      <span class="brand-name">Brightfen</span>
      <span class="brand-tagline">Environmental Credit Company</span>
    </div>

    <div class="divider"></div>

    <div class="person">
      <p class="person-name"><span class="person-first">Mira</span> <span class="person-last">Kovalenko</span></p>
      <p class="person-title">Managing Director</p>
      <ul class="contact-list">
        <li class="contact-item">
          <svg class="contact-icon" viewBox="0 0 24 24" aria-hidden="true"><path d="M6.6 10.8a15.1 15.1 0 0 0 6.6 6.6l2.2-2.2a1 1 0 0 1 1-.25 11.4 11.4 0 0 0 3.6.57 1 1 0 0 1 1 1V20a1 1 0 0 1-1 1A17 17 0 0 1 3 4a1 1 0 0 1 1-1h3.5a1 1 0 0 1 1 1c0 1.25.2 2.45.57 3.57a1 1 0 0 1-.25 1z"/></svg>
          <span>(555) 214-0387</span>
        </li>
        <li class="contact-item">
          <svg class="contact-icon" viewBox="0 0 24 24" aria-hidden="true"><path d="M2 5h20v14H2z M4 7v.5l8 5 8-5V7l-8 5z" fill-rule="evenodd"/></svg>
          <span>hello@brightfen.co</span>
        </li>
        <li class="contact-item">
          <svg class="contact-icon" viewBox="0 0 24 24" aria-hidden="true"><circle cx="12" cy="12" r="10"/></svg>
          <span>www.brightfen.co</span>
        </li>
      </ul>
    </div>
  </section>

</body>
</html>
```